New Business Card Design for Manufacturing

We are an engineering/manufacturing company that offers Advanced machining/assembly/engineering services, as well as innovative products for the heavy duty engine cooling markets.

We are looking to get a new business card designed that is clean and modern looking, but still fits the wide range of technical/skilled work we do.

- We hope to use this design as the base for other design work in new Presentations, web, and print work.

Industry/Entity Type

Engineering

Contact Information for Business Card

Our preferred color of blue is (RGB) 22/71/159 but can vary slightly from that color. Our content will be our Logo and full company name (Vantrell Forge Works, Inc.), company address, name, job title, phone number with extension, cell number, fax number, website, and email address on the cards.
We'd like the full company name next to the logo, but we are open to other interpretations of that layout.
Preferably, we would like the back side to be clean with just our logo, and the front to contain all of the contact information.

Colors
2f74b4
0355a3
85abd2

Requirements
Must have
• - Logo, company name, needed content - We are open to interpretation beyond that.
• - Standard size business card.
• - Horizontal orientation.
• - Enough space for lengthy names / job titles (for example, a job title could read "Directory of Human Resources" or "V.P. of Governmental Affairs"). We need this to look clean, whether the title be short (CEO) or long (as described above).

```html
<!DOCTYPE html>
<html lang="en">
<head>
<meta charset="utf-8">
<title>Vantrell Forge Works – Business Card</title>
<link rel="stylesheet" href="https://fonts.googleapis.com/css2?family=Lato:wght@400;700;900&display=swap">
<style>
  :root {
    --stage: #2b2b2d;
    --card: #0b0b0c;
    --blue: #16479f;
    --blue-bright: #1f5fc4;
    --blue-soft: #85abd2;
    --grey: #9aa1a8;
    --white: #f2f2f2;
  }
  * { box-sizing: border-box; margin: 0; padding: 0; }
  html, body { width: 1200px; height: 852px; overflow: hidden; }
  body {
    background: var(--stage);
    font-family: "Lato", sans-serif;
    position: relative;
  }
  .card {
    position: absolute;
    left: 280px;
    width: 640px;
    height: 366px;
    background: var(--card);
    border-radius: 18px;
    overflow: hidden;
    box-shadow: 0 10px 30px rgba(0,0,0,.45);
  }
  .card--back { top: 40px; }
  .card--front { top: 446px; }

  .brand { position: absolute; display: flex; flex-direction: column; gap: 8px; }
  .brand__name {
    display: flex; align-items: center; gap: 10px;
    font-weight: 900; color: var(--blue-bright);
    text-transform: uppercase; letter-spacing: .5px; line-height: 1;
  }
  .brand__square { background: var(--blue-bright); flex: none; }
  .brand__tagline {
    color: var(--grey); font-weight: 700; text-transform: uppercase;
    letter-spacing: 1.5px;
  }

  .card--back .brand { left: 110px; top: 140px; }
  .card--back .brand__name { font-size: 34px; }
  .card--back .brand__square { width: 26px; height: 26px; }
  .card--back .brand__tagline { font-size: 13px; padding-left: 36px; }
  .card--back .website {
    position: absolute; right: 110px; bottom: 70px;
    color: var(--white); font-size: 14px; letter-spacing: 1.5px;
  }

  .card--front .brand { left: 200px; top: 58px; }
  .card--front .brand__name { font-size: 26px; }
  .card--front .brand__square { width: 20px; height: 20px; }
  .card--front .brand__tagline { font-size: 11px; padding-left: 30px; }

  .rule { position: absolute; height: 1.5px; background: var(--blue-bright); }
  .rule--top { left: 28px; right: 28px; top: 150px; }
  .rule--name { left: 40px; width: 250px; top: 240px; }

  .person { position: absolute; left: 40px; top: 180px; }
  .person__name {
    color: var(--blue-bright); font-size: 24px; letter-spacing: 1.5px;
    text-transform: uppercase; font-weight: 400;
  }
  .person__title { color: var(--white); font-size: 14px; margin-top: 3px; }

  .contacts { position: absolute; left: 40px; top: 252px; list-style: none; }
  .contacts li {
    display: flex; align-items: center; gap: 10px;
    color: var(--white); font-size: 13px; line-height: 18px;
  }
  .contacts svg { width: 10px; height: 10px; fill: var(--blue-bright); flex: none; }

  .address {
    position: absolute; right: 40px; top: 180px; text-align: right;
    color: var(--white); font-size: 14px; line-height: 20px;
  }
  .address .website { margin-top: 10px; font-weight: 700; }
  .address .website span { color: var(--blue-bright); font-weight: 400; }

  .edge { position: absolute; left: 0; bottom: 0; width: 640px; height: 70px; }
</style>
</head>
<body>
  <section class="card card--back" aria-label="Card back">
    <div class="brand">
      <div class="brand__name"><span class="brand__square"></span>Vantrell Forge Works, Inc.</div>
      <div class="brand__tagline">Built for What's Next</div>
    </div>
    <div class="website">www.yourwebsite.com</div>
  </section>

  <section class="card card--front" aria-label="Card front">
    <div class="brand">
      <div class="brand__name"><span class="brand__square"></span>Vantrell Forge Works, Inc.</div>
      <div class="brand__tagline">Built for What's Next</div>
    </div>
    <div class="rule rule--top"></div>

    <div class="person">
      <div class="person__name">Dorian Kessler</div>
      <div class="person__title">Directory of Human Resources</div>
    </div>
    <div class="rule rule--name"></div>

    <ul class="contacts">
      <li><svg viewBox="0 0 10 10"><path d="M2 0h2l1 3-1.5 1a6 6 0 0 0 2.5 2.5L7 5l3 1v2a2 2 0 0 1-2 2A8 8 0 0 1 0 2a2 2 0 0 1 2-2z"/></svg>1234- ext</li>
      <li><svg viewBox="0 0 10 10"><rect x="2" y="0" width="6" height="10" rx="1"/></svg>555-318-4402</li>
      <li><svg viewBox="0 0 10 10"><rect x="1" y="3" width="8" height="5" rx="1"/><rect x="3" y="0" width="4" height="3"/></svg>(555)318-4490</li>
      <li><svg viewBox="0 0 10 10"><path d="M0 2h10v6H0z M0 2l5 3.5L10 2" /></svg>d.kessler@vantrellforge.com</li>
    </ul>

    <div class="address">
      <div>4870 Harlow Industrial Pkwy.</div>
      <div>Dunmore Falls, FL 33412</div>
      <div class="website">www.<span>VantrellForge</span>.com</div>
    </div>

    <svg class="edge" viewBox="0 0 640 70" preserveAspectRatio="none" aria-hidden="true">
      <path d="M0 50 H420 Q440 50 452 38 L468 22 Q478 12 494 12 H640 V70 H0 Z" fill="var(--blue-bright)"/>
      <path d="M0 44 H418 Q432 44 442 36 L448 31 Q436 50 420 50 H0 Z" fill="var(--grey)"/>
    </svg>
  </section>
</body>
</html>
```